At Home Pet Euthanasia - business cards & brand stationary

We already have a logo and the colors and a website. Need a business card designed that will be able to customized to multiple veterinarians who will be partnering with us. The feel needs to be compassionate, comforting with our tagline 'A Gift of Love at Home'. It will be 2 sides.
On the back our platform/partner vets will be customizing each business card with their own service areas, phone numbers, name and title. On the front, i would like to see experimentation with use of our photos, the logo, tagline and a description 'Peaceful and Compassionate At-Home Pet Euthanasia'

```html
<!DOCTYPE html>
<html lang="en">
<head>
<meta charset="utf-8">
<title>Hearthpaw business card</title>
<link rel="stylesheet" href="https://fonts.googleapis.com/css2?family=Poppins:wght@300;400;500;600&display=swap">
<style>
  :root {
    --brand-blue: #7399c6;
    --ink: #1c1c1c;
    --paper: #f7f7f7;
    --backdrop: #e4e4e4;
    --white: #ffffff;
    --photo-rose: #e9a9a3;
    --photo-skin: #e6c1ac;
    --photo-grey: #b9b7b4;
  }
  * { box-sizing: border-box; margin: 0; padding: 0; }
  html, body { width: 1200px; height: 930px; overflow: hidden; }
  body {
    background: var(--backdrop);
    font-family: "Poppins", sans-serif;
    color: var(--ink);
    position: relative;
  }
  .card {
    position: absolute;
    top: 310px;
    width: 540px;
    height: 309px;
    border-radius: 3px;
    overflow: hidden;
    box-shadow: 0 6px 18px rgba(0,0,0,0.12);
  }
  .card--details { left: 40px; background: var(--paper); }
  .card--photo { left: 620px; }

  .brand {
    position: absolute;
    top: 34px;
    left: 0; right: 0;
    display: flex;
    justify-content: center;
    align-items: center;
    gap: 12px;
  }
  .brand__mark {
    width: 30px; height: 30px;
    background: var(--brand-blue);
  }
  .brand__name {
    font-weight: 600;
    font-size: 42px;
    color: var(--brand-blue);
    line-height: 1;
  }
  .brand__tagline {
    position: absolute;
    top: 88px; left: 0; right: 0;
    text-align: center;
    font-weight: 300;
    font-size: 13px;
    color: var(--brand-blue);
    letter-spacing: 0.3px;
  }
  .person {
    position: absolute;
    top: 118px; left: 0; right: 0;
    text-align: center;
  }
  .person__name {
    font-weight: 600;
    font-size: 20px;
    color: var(--brand-blue);
    line-height: 1.2;
  }
  .person__title {
    font-size: 13px;
    line-height: 1.3;
  }
  .contact {
    position: absolute;
    top: 178px; left: 0; right: 0;
    display: flex;
    justify-content: center;
    gap: 16px;
    font-size: 12.5px;
    line-height: 1.45;
  }
  .contact__address { text-align: right; }
  .contact__divider { width: 1px; background: var(--ink); }
  .contact__list { list-style: none; }
  .contact__list li { display: flex; align-items: center; gap: 6px; }
  .contact__list svg { width: 11px; height: 11px; fill: var(--brand-blue); flex: none; }
  .band {
    position: absolute;
    left: 0; right: 0; bottom: 0;
    height: 28px;
    background: var(--brand-blue);
    color: var(--white);
    font-size: 12px;
    letter-spacing: 0.6px;
    display: flex;
    align-items: center;
    justify-content: center;
  }

  .photo {
    position: absolute; inset: 0;
    background: linear-gradient(115deg, var(--photo-grey) 0%, var(--photo-rose) 30%, var(--photo-skin) 55%, var(--photo-grey) 85%);
  }
  .card--photo .brand {
    top: auto; bottom: 70px; left: 70px; right: auto;
    justify-content: flex-start;
  }
  .card--photo .brand__mark { background: var(--white); }
  .card--photo .brand__name { color: var(--white); }
</style>
</head>
<body>
  <section class="card card--details">
    <div class="brand">
      <span class="brand__mark"></span>
      <span class="brand__name">Hearthpaw</span>
    </div>
    <p class="brand__tagline">A gift of love at home.</p>
    <div class="person">
      <p class="person__name">Daniel Morrow</p>
      <p class="person__title">Managing Director</p>
    </div>
    <div class="contact">
      <p class="contact__address">88, Willow Lane<br>Suite two<br>30917, Country Name</p>
      <span class="contact__divider"></span>
      <ul class="contact__list">
        <li><svg viewBox="0 0 24 24" aria-hidden="true"><path d="M6.6 10.8a15 15 0 0 0 6.6 6.6l2.2-2.2a1 1 0 0 1 1-.25 11.4 11.4 0 0 0 3.6.57 1 1 0 0 1 1 1V20a1 1 0 0 1-1 1A17 17 0 0 1 3 4a1 1 0 0 1 1-1h3.5a1 1 0 0 1 1 1c0 1.25.2 2.45.57 3.57a1 1 0 0 1-.25 1z"/></svg>055-987 654 321</li>
        <li><svg viewBox="0 0 24 24" aria-hidden="true"><path d="M2 5h20v14H2zm2 2v.5l8 5 8-5V7z"/></svg>info@hearthpawcare.com</li>
        <li><svg viewBox="0 0 24 24" aria-hidden="true"><path d="M12 2a10 10 0 1 0 0 20 10 10 0 0 0 0-20zm-1 17.9A8 8 0 0 1 4.1 13H8c.1 2.5.9 4.9 3 6.9zM8 11H4.1A8 8 0 0 1 11 4.1C8.9 6.1 8.1 8.5 8 11zm2 0c.1-2.3 1-4.4 2-5.8 1 1.4 1.9 3.5 2 5.8zm0 2h4c-.1 2.3-1 4.4-2 5.8-1-1.4-1.9-3.5-2-5.8zm3 6.9c2.1-2 2.9-4.4 3-6.9h3.9a8 8 0 0 1-6.9 6.9zM16 11c-.1-2.5-.9-4.9-3-6.9a8 8 0 0 1 6.9 6.9z"/></svg>www.hearthpawcare.com</li>
      </ul>
    </div>
    <p class="band">PEACEFUL AND COMPASSIONATE AT-HOME PET EUTHANASIA</p>
  </section>

  <section class="card card--photo">
    <div class="photo" role="img" aria-label="Photo of a child in a pink top gently hugging a blue-eyed tabby cat"></div>
    <div class="brand">
      <span class="brand__mark"></span>
      <span class="brand__name">Hearthpaw</span>
    </div>
  </section>
</body>
</html>
```